KTR Photography Editing & Support Services for Real Estate

We require a double sided A4 flyer to promote our photography services to real estate agencies.
This particular service is targeted to rural areas where reliable, professional and highly skilled photographers are difficult to source. We teach the agent how to photograph, they upload files to a server and we take care of the rest (image editing, quality control and delivery). This will give the agents flexibility with when to shoot and eliminates the stress of managing a photographer / contractor. We offer a 1 day face to face training session and competitive packages for equipment start up.
We would like the flyer to look clean & very professional. The flyer should showcase samples of our work to highlight what can be achieved by using our services. We like the look of a black or dark background behind the text and feel that would look nice with our photographs provided. Otherwise open to your suggestions and ideas.
TEXT FOR FLYER:
Welcome to the KTR Real Estate Photography Editing and Support Service
• Take your real estate business to the next level by providing impressive real estate imagery that makes you stands out from the competition
• Omit the stress of trying to find a good photographer or managing an unreliable one and hence have more time to focus on other aspects of your business
• Showcase your listings with better quality and more impactful photographs than your competitors thereby increasing potential for a quick sale
• Great first impressions matter and you will achieve this by looking and feeling more professional. This will attract and retain more future clients.
HOW IT WORKS
• We understand that your time is valuable, so let us handle the editing and delivery of your images. You shoot, and we take care of the rest.
• Images are edited and delivered within 1 working day
INCLUSIONS:
• Full day face to face training (we come to you) and instructional handbook
• We will teach you everything you need to know about your equipment and how to take stunning real estate photographs
• Service turnaround within 1 working day
• Free HELP desk service Mon-Fri
• 12 month Exclusivity (rural towns only) for a limited time
INVESTMENT
• 99 per listing for us to manage images including editing, quality control and delivery (10 Images)
• Ask us about competitive packages for photography equipment if required
SUMMARY
The KTR Real Estate Photography Editing and Support Service is the perfect solution for busy real estate professionals who want to take their business to the next level. Our service is affordable, flexible, and designed to help you showcase your listings in the best possible light.
Contact us today to learn more about how we can help you.

```html
<!DOCTYPE html>
<html lang="en">
<head>
<meta charset="utf-8">
<title>KTR Real Estate Photography Editing and Support Service – Flyer</title>
<link href="https://fonts.googleapis.com/css2?family=Poppins:wght@400;500;600;700&family=Bebas+Neue&display=swap" rel="stylesheet">
<style>
:root{
  --navy:#0f2552;
  --navy-deep:#0a1a3d;
  --ink:#111111;
  --paper:#ffffff;
  --canvas:#e4e5e8;
  --rule:#c9ccd3;
  --text:#1d1d1f;
}
*{box-sizing:border-box;margin:0;padding:0}
html,body{width:816px;height:1200px;overflow:hidden;background:var(--canvas)}
body{font-family:"Poppins",Arial,sans-serif;color:var(--text);position:relative}
.sheet-slot{position:absolute;left:178px;width:460px;height:589px;box-shadow:0 6px 18px rgba(0,0,0,.18)}
.sheet-slot.front{top:6px}
.sheet-slot.back{top:605px}
.sheet{position:absolute;left:0;top:0;width:600px;height:768px;background:var(--paper);transform:scale(.7667);transform-origin:0 0;overflow:hidden}
.abs{position:absolute}
.photo{position:absolute}
.footer-stripe{position:absolute;left:0;right:0;bottom:0;height:7px;background:var(--navy)}

/* front */
.brand-mark{left:28px;top:52px;width:140px;text-align:center;font-weight:600;color:var(--ink);font-size:13px;letter-spacing:2px;line-height:1.2}
.brand-mark small{display:block;font-size:6.5px;letter-spacing:2px;font-weight:500;margin-top:4px;color:#555}
.title-kicker{left:178px;top:52px;width:388px;height:19px;background:var(--navy);color:#fff;font-weight:600;font-size:13.5px;letter-spacing:3px;text-align:center;line-height:19px;white-space:nowrap}
.title-main{left:178px;top:73px;width:390px;font-family:"Bebas Neue","Arial Narrow",sans-serif;font-weight:400;font-size:27px;color:var(--ink);letter-spacing:0;line-height:30px;white-space:nowrap;text-align:center}
.hero-band{left:0;top:255px;width:600px;height:250px;background:var(--navy)}
.hero-frame{left:30px;top:112px;width:542px;height:274px;background:var(--paper);border:4px solid var(--navy);padding:4px}
.hero-frame .photo{left:4px;top:4px;right:4px;bottom:4px;background:linear-gradient(180deg,#8fa6c4 0%,#d9c8b8 38%,#2e3442 60%,#4d5a3a 80%,#6e7a4a 100%)}
.benefits{left:35px;top:402px;width:540px;display:grid;grid-template-columns:1fr 1fr;column-gap:24px;row-gap:12px;list-style:none}
.benefits li{position:relative;padding-left:15px;color:#fff;font-size:8.4px;line-height:1.25}
.tick{position:absolute;left:0;top:1px;width:9px;height:9px}

.section-head{font-weight:700;font-size:18px;color:var(--ink);letter-spacing:.2px}
.section-rule{height:1px;background:#555}
.how-head{left:37px;top:518px}
.how-rule{left:37px;top:542px;width:255px}
.steps{left:37px;top:552px;width:255px;list-style:none}
.steps li{position:relative;padding-left:46px;font-size:8.4px;line-height:1.25;min-height:32px;padding-bottom:10px;margin-bottom:12px;border-bottom:1px solid var(--rule)}
.steps li:last-child{border-bottom:none}
.icon-box{position:absolute;left:4px;top:0;width:30px;height:30px;border-radius:6px;background:var(--ink);box-shadow:2px 2px 0 #9aa0aa}
.icon-box svg{width:30px;height:30px}

.contact{left:35px;top:655px;width:260px;height:95px}
.contact .avatar{position:absolute;left:0;top:0;width:72px;height:72px;border-radius:50%;border:3px solid var(--ink);background:radial-gradient(circle at 50% 40%,#b89a86 0%,#6a5448 55%,#1b1b1b 100%)}
.contact .nameplate{position:absolute;left:55px;top:13px;width:180px;height:34px;background:var(--ink);border-radius:0 6px 6px 0;color:#fff;padding:3px 0 0 30px;line-height:1.1}
.nameplate b{display:block;font-size:13px;font-weight:700}
.nameplate span{font-size:10.5px;font-weight:500}
.contact .lines{position:absolute;left:84px;top:52px;font-size:10px;font-weight:600;line-height:17px;color:var(--ink);white-space:nowrap}
.lines svg{width:10px;height:10px;vertical-align:-1px;margin-right:4px}

/* back */
.intro-panel{left:0;top:0;width:248px;height:235px;background:var(--navy)}
.intro-stripes{left:0;top:0;width:46px;height:235px;background:repeating-linear-gradient(90deg,#1a1d24 0 12px,#2a2e38 12px 14px)}
.intro-copy{left:70px;top:42px;width:178px;color:#fff;font-size:12.4px;font-weight:500;line-height:1.15}
.coast-photo{left:248px;top:0;width:352px;height:235px;background:linear-gradient(180deg,#c4c9dc 0%,#e6c9c0 30%,#4f6b86 52%,#8a6a3d 70%,#4f6b2f 100%)}
.bedroom-photo{left:0;top:243px;width:280px;height:115px;background:linear-gradient(135deg,#eceae6 0%,#b9bcb9 50%,#6e7a72 100%)}
.invest-box{left:280px;top:243px;width:320px;height:115px;background:var(--ink);color:#fff;padding:14px 24px 0 30px}
.invest-box h2{font-size:18px;font-weight:700;margin-bottom:6px}
.invest-box ul{list-style:none}
.invest-box li{position:relative;padding-left:14px;font-size:8.4px;line-height:1.2;margin-bottom:8px}
.inc-head{left:35px;top:378px}
.inc-rule{left:35px;top:402px;width:255px}
.inclusions{left:35px;top:410px;width:255px;list-style:none}
.inclusions li{position:relative;padding-left:46px;font-size:8.4px;line-height:1.25;height:44px;padding-top:3px;margin-bottom:4px;border-bottom:1px solid var(--rule)}
.inclusions li.single{padding-top:10px}
.inclusions li:last-child{border-bottom:none}
.gallery-a{left:312px;top:375px;width:254px;height:117px;background:linear-gradient(180deg,#7a5a3a 0%,#2f4f7a 45%,#3a2e22 100%)}
.gallery-b{left:312px;top:500px;width:254px;height:117px;background:linear-gradient(180deg,#7a86a8 0%,#c9c9cc 45%,#b58a4a 75%,#4a4a3a 100%)}
.gallery-c{left:312px;top:625px;width:254px;height:117px;background:linear-gradient(180deg,#efefed 0%,#dcd8d0 55%,#b08a62 100%)}
.hall-photo{left:310px;top:515px;width:127px;height:93px;background:linear-gradient(180deg,#d7d2c8 0%,#8a7a66 100%)}
.bath-photo{left:441px;top:515px;width:124px;height:93px;background:linear-gradient(180deg,#e3ded7 0%,#c7b9a6 100%)}
.lounge-photo{left:310px;top:614px;width:255px;height:126px;background:linear-gradient(180deg,#3b3f47 0%,#24262b 55%,#8a8170 100%)}
</style>
</head>
<body>

<svg width="0" height="0" style="position:absolute" aria-hidden="true">
  <defs>
    <symbol id="tick-dot" viewBox="0 0 10 10"><circle cx="5" cy="5" r="5" fill="#fff"/><path d="M2.7 5.2l1.6 1.6 3-3.2" stroke="#0f2552" stroke-width="1.3" fill="none"/></symbol>
    <symbol id="tick-dot-dark" viewBox="0 0 10 10"><circle cx="5" cy="5" r="5" fill="#fff"/><path d="M2.7 5.2l1.6 1.6 3-3.2" stroke="#111" stroke-width="1.3" fill="none"/></symbol>
  </defs>
</svg>

<!-- Front side -->
<section class="sheet-slot front">
  <div class="sheet">
    <div class="abs brand-mark">DANA MARLOWE<small>PHOTOGRAPHER</small></div>
    <div class="abs title-kicker">WELCOME TO THE KTR REAL ESTATE</div>
    <h1 class="abs title-main">PHOTOGRAPHY EDITING AND SUPPORT SERVICE</h1>

    <div class="abs hero-band"></div>
    <div class="abs hero-frame"><div class="photo" role="img" aria-label="Dusk photograph of a dark weatherboard country home with lit porch and garden path"></div></div>

    <ul class="abs benefits">
      <li><svg class="tick"><use href="#tick-dot"/></svg>Take your real estate business to the next level by providing impressive real estate imagery that makes you stands out from the competition</li>
      <li><svg class="tick"><use href="#tick-dot"/></svg>Showcase your listings with better quality and more impactful photographs than your competitors thereby increasing potential for a quick sale</li>
      <li><svg class="tick"><use href="#tick-dot"/></svg>Omit the stress of trying to find a good photographer or managing an unreliable one and hence have more time to focus on other aspects of your business</li>
      <li><svg class="tick"><use href="#tick-dot"/></svg>Great first impressions matter and you will achieve this by looking and feeling more professional. This will attract and retain more future clients</li>
    </ul>

    <h2 class="abs section-head how-head">HOW IT WORKS</h2>
    <div class="abs section-rule how-rule"></div>
    <ul class="abs steps">
      <li><span class="icon-box"><svg viewBox="0 0 30 30"><rect x="8" y="9" width="14" height="12" rx="1.5" fill="none" stroke="#fff" stroke-width="1.6"/><path d="M10 19l4-4 3 3 2-2 2 3" stroke="#fff" stroke-width="1.4" fill="none"/></svg></span>We understand that your time is valuable, so let us handle the editing and delivery of your images. You shoot, and we take care of the rest.</li>
      <li><span class="icon-box"><svg viewBox="0 0 30 30"><rect x="7" y="11" width="11" height="8" fill="#fff"/><path d="M18 13h3l3 3v3h-6z" fill="#fff"/><circle cx="11" cy="20" r="2" fill="#111" stroke="#fff"/><circle cx="21" cy="20" r="2" fill="#111" stroke="#fff"/></svg></span>Images are edited and delivered within 1 working day</li>
    </ul>

    <div class="photo hall-photo" role="img" aria-label="Interior hallway photograph"></div>
    <div class="photo bath-photo" role="img" aria-label="Bathroom photograph with freestanding bath"></div>
    <div class="photo lounge-photo" role="img" aria-label="Living room photograph with dark sofa and side table"></div>

    <div class="abs contact">
      <div class="avatar" role="img" aria-label="Portrait of the photographer"></div>
      <div class="nameplate"><b>DANA MARLOWE</b><span>PHOTOGRAPHY</span></div>
      <div class="lines">
        <div><svg viewBox="0 0 10 10"><circle cx="5" cy="5" r="5" fill="#0f2552"/><path d="M3.2 2.8l1 1-.5.7a4 4 0 0 0 1.8 1.8l.7-.5 1 1-.7.7C4.8 7.3 2.7 5.2 2.5 3.5z" fill="#fff"/></svg>+61 400 555 019</div>
        <div><svg viewBox="0 0 10 10"><circle cx="5" cy="5" r="5" fill="#0f2552"/><rect x="2.6" y="3.3" width="4.8" height="3.4" fill="#fff"/><path d="M2.6 3.3L5 5.2l2.4-1.9" stroke="#0f2552" stroke-width=".7" fill="none"/></svg>hello@danamarlowe.com.au</div>
      </div>
    </div>
    <div class="footer-stripe"></div>
  </div>
</section>

<!-- Back side -->
<section class="sheet-slot back">
  <div class="sheet">
    <div class="abs intro-panel"></div>
    <div class="abs intro-stripes"></div>
    <p class="abs intro-copy">The KTR Real Estate Photography Editing and Support Service is the perfect solution for busy real estate professionals who want to take their business to the next level. Our service is affordable, flexible, and designed to help you showcase your listings in the best possible light</p>
    <div class="photo coast-photo" role="img" aria-label="Coastal cliff headland at sunset over the ocean"></div>

    <div class="photo bedroom-photo" role="img" aria-label="Bright bedroom with large windows overlooking the countryside"></div>
    <div class="abs invest-box">
      <h2>INVESTMENT</h2>
      <ul>
        <li><svg class="tick"><use href="#tick-dot-dark"/></svg>99 per listing for us to manage images including editing, quality control and delivery (10 Images)</li>
        <li><svg class="tick"><use href="#tick-dot-dark"/></svg>Ask us about competitive packages for photography equipment if required</li>
      </ul>
    </div>

    <h2 class="abs section-head inc-head">INCLUSIONS</h2>
    <div class="abs section-rule inc-rule"></div>
    <ul class="abs inclusions">
      <li><span class="icon-box"><svg viewBox="0 0 30 30"><circle cx="13" cy="9" r="2.2" fill="#fff"/><path d="M13 12v7l-3 4M13 19l3 4M10 14h6" stroke="#fff" stroke-width="1.6" fill="none"/><rect x="18" y="10" width="5" height="8" fill="none" stroke="#fff" stroke-width="1.2"/></svg></span>Full day face to face training (we come to you) and instructional handbook</li>
      <li><span class="icon-box"><svg viewBox="0 0 30 30"><circle cx="15" cy="11" r="3.5" fill="#fff"/><path d="M9 23c0-4 2.5-6.5 6-6.5s6 2.5 6 6.5z" fill="#fff"/></svg></span>We will teach you everything you need to know about your equipment and how to take stunning real estate photographs</li>
      <li class="single"><span class="icon-box"><svg viewBox="0 0 30 30"><circle cx="15" cy="15" r="7" fill="none" stroke="#fff" stroke-width="2.4" stroke-dasharray="3 2"/><circle cx="15" cy="15" r="2.5" fill="#fff"/></svg></span>Service turnaround within 1 working day</li>
      <li class="single"><span class="icon-box"><svg viewBox="0 0 30 30"><path d="M9 16a6 6 0 0 1 12 0" stroke="#fff" stroke-width="1.8" fill="none"/><rect x="8" y="15" width="3" height="5" rx="1" fill="#fff"/><rect x="19" y="15" width="3" height="5" rx="1" fill="#fff"/></svg></span>Free HELP desk service Mon-Fri</li>
      <li><span class="icon-box"><svg viewBox="0 0 30 30"><rect x="8" y="9" width="14" height="13" rx="1" fill="none" stroke="#fff" stroke-width="1.6"/><path d="M8 13h14M11 7v4M19 7v4" stroke="#fff" stroke-width="1.6"/></svg></span>12 month Exclusivity (rural towns only) for a limited time</li>
    </ul>

    <div class="photo gallery-a" role="img" aria-label="Timber-lined living room with tall windows at dusk"></div>
    <div class="photo gallery-b" role="img" aria-label="Modern gabled home exterior lit at twilight"></div>
    <div class="photo gallery-c" role="img" aria-label="White kitchen and dining area with timber floor"></div>

    <div class="abs contact">
      <div class="avatar" role="img" aria-label="Portrait of the photographer"></div>
      <div class="nameplate"><b>DANA MARLOWE</b><span>PHOTOGRAPHY</span></div>
      <div class="lines">
        <div><svg viewBox="0 0 10 10"><circle cx="5" cy="5" r="5" fill="#0f2552"/><path d="M3.2 2.8l1 1-.5.7a4 4 0 0 0 1.8 1.8l.7-.5 1 1-.7.7C4.8 7.3 2.7 5.2 2.5 3.5z" fill="#fff"/></svg>+61 400 555 019</div>
        <div><svg viewBox="0 0 10 10"><circle cx="5" cy="5" r="5" fill="#0f2552"/><rect x="2.6" y="3.3" width="4.8" height="3.4" fill="#fff"/><path d="M2.6 3.3L5 5.2l2.4-1.9" stroke="#0f2552" stroke-width=".7" fill="none"/></svg>hello@danamarlowe.com.au</div>
      </div>
    </div>
    <div class="footer-stripe"></div>
  </div>
</section>

</body>
</html>
```